Business Card Design

I need business cards designed for a new company i have started that makes cakes, particularly themed kids cakes with a really modern design and I would like to have my business cards reflect this. I have attached some photos of cakes I have made and would like some to be used.

Industry/Entity Type

Business

Contact Information for Business Card

Business Name: Tarts and Treats by Maren
Mobile: 0492 815 063
email: maren@tartsandtreatsbymaren.example.au
Instagram: instagram.com/tartsandtreatsbymaren/
Facebook: fb.me/tartsandtreatsbymaren

Colors
e667a6
b768aa
3276b5

Requirements
Must have
• Business Name: Tarts and Treats by Maren
• Mobile: 0492 815 063
• email: maren@tartsandtreatsbymaren.example.au
• Instagram: instagram.com/tartsandtreatsbymaren/
• Facebook: fb.me/tartsandtreatsbymaren
Nice to have
• 2 to 3 pictures of my cakes

```html
<!DOCTYPE html>
<html lang="en">
<head>
<meta charset="utf-8">
<title>Tarts and Treats by Maren — Business Card</title>
<link rel="stylesheet" href="https://fonts.googleapis.com/css2?family=Open+Sans:wght@400;600;700&display=swap">
<style>
  :root {
    --backdrop: #ecebef;
    --pink: #e667a6;
    --pink-light: #f08fc0;
    --purple: #b768aa;
    --purple-deep: #9a4f90;
    --lavender: #d7b8dc;
    --white: #ffffff;
    --paper: #f4f4f6;
  }
  * { box-sizing: border-box; margin: 0; padding: 0; }
  html, body {
    width: 1200px; height: 843px; overflow: hidden;
    background: var(--backdrop);
    font-family: "Open Sans", Arial, sans-serif;
  }
  .sheet {
    width: 1200px; height: 843px;
    display: flex; flex-direction: column;
    align-items: center; justify-content: center; gap: 36px;
  }
  .card {
    position: relative;
    width: 640px; height: 366px;
    border-radius: 4px; overflow: hidden;
    box-shadow: 0 6px 18px rgba(60, 30, 70, 0.18);
  }
  /* Back side */
  .card--back {
    background: linear-gradient(120deg, var(--purple) 0%, #c27cb6 45%, var(--purple-deep) 100%);
    display: flex; align-items: center; justify-content: center;
  }
  .wordmark {
    display: flex; align-items: center; gap: 14px;
    font-weight: 600; line-height: 1.1; text-align: center;
  }
  .wordmark__dot {
    width: 22px; height: 22px; border-radius: 50%; flex: none;
  }
  .card--back .wordmark { color: var(--white); font-size: 38px; }
  .card--back .wordmark__dot { background: var(--white); }

  /* Front side */
  .card--front { background: linear-gradient(90deg, var(--paper), var(--white)); }
  .card__shapes { position: absolute; inset: 0; }
  .person {
    position: absolute; left: 34px; top: 34px; color: var(--white);
  }
  .person__name { font-size: 18px; font-weight: 700; letter-spacing: 0.5px; }
  .person__role { font-size: 13px; font-weight: 400; margin-top: 2px; }
  .contact {
    position: absolute; left: 30px; top: 226px;
    list-style: none; color: var(--white);
    font-size: 12.5px; line-height: 20px;
  }
  .card--front .wordmark {
    position: absolute; left: 390px; top: 145px; width: 230px;
    color: var(--pink); font-size: 27px;
  }
  .card--front .wordmark__dot { background: var(--purple); width: 18px; height: 18px; }
</style>
</head>
<body>
<main class="sheet">
  <section class="card card--back" aria-label="Card back">
    <div class="wordmark">
      <span class="wordmark__dot"></span>
      <span>Tarts and Treats<br>by Maren</span>
    </div>
  </section>

  <section class="card card--front" aria-label="Card front">
    <svg class="card__shapes" viewBox="0 0 640 366" width="640" height="366" aria-hidden="true">
      <defs>
        <linearGradient id="pinkPanel" x1="0" y1="0" x2="1" y2="0">
          <stop offset="0" stop-color="#e667a6"/>
          <stop offset="1" stop-color="#f08fc0"/>
        </linearGradient>
      </defs>
      <path d="M0 0 H402 Q300 170 290 366 H0 Z" fill="url(#pinkPanel)"/>
      <path d="M402 0 H412 Q312 170 304 366 H290 Q300 170 402 0 Z" fill="#b768aa"/>
      <path d="M416 0 Q318 170 310 366" fill="none" stroke="#d7b8dc" stroke-width="2"/>
    </svg>

    <div class="person">
      <p class="person__name">DANA WHITLOCK</p>
      <p class="person__role">CEO/Founder</p>
    </div>

    <ul class="contact">
      <li>Mob: 0492 815 063</li>
      <li>maren@tartsandtreatsbymaren.example.au</li>
      <li>Ins: tartsandtreatsbymaren</li>
      <li>Fb: tartsandtreatsbymaren</li>
    </ul>

    <div class="wordmark">
      <span class="wordmark__dot"></span>
      <span>Tarts and Treats<br>by Maren</span>
    </div>
  </section>
</main>
</body>
</html>
```